Business Card for beauty technology startup

Design Glimora Business Card for a Beauty, based on the website identity and colors (https://www.glimora-example.com).
Glimora is a beauty tech startup that gathers helpful product info for beauty lovers and consumers (such as availability on stores, price range and product reviews) for makeup products. The card design must be young, colorful but clean, and very modern.

Target Market(s)

woman, 15-35

Industry/Entity Type

Cosmetics

Contact Information for Business Card

Full Name, address, phone

Font styles to use
Other font styles liked:
• Advent Pro

Colors
e34297
86cfc6
ffffff
5c5c5c
e8e8e8
e667a6
b2b2b2

Requirements
Must have
• One full colored side with a creative design and another with card info
• Use Color palette: #95C5C5 and/or #D38AA5
• Use fonts: Advent Pro
• Use website identity: https://www.glimora-example.com
Nice to have
• If needed extra font: Roboto

```html
<!DOCTYPE html>
<html lang="en">
<head>
<meta charset="utf-8">
<title>Glimora Business Card</title>
<link rel="stylesheet" href="https://fonts.googleapis.com/css2?family=Advent+Pro:wght@300;400&family=Roboto:wght@400;500;700&display=swap">
<style>
  :root {
    --canvas: #dcdcdc;
    --rose: #b97c93;
    --rose-light: #d9b3c1;
    --paper: #f4f4f4;
    --ink: #4a4a4a;
    --night: #1b1c1e;
    --white: #ffffff;
  }
  * { margin: 0; padding: 0; box-sizing: border-box; }
  html, body { width: 1200px; height: 960px; overflow: hidden; }
  body {
    position: relative;
    background: var(--canvas);
    font-family: "Roboto", sans-serif;
  }
  .card {
    position: absolute;
    border-radius: 22px;
    overflow: hidden;
    box-shadow: 0 4px 10px rgba(0,0,0,0.25);
  }
  .card-front {
    left: 313px; top: 113px; width: 602px; height: 343px;
    background: var(--paper);
  }
  .front-band {
    position: absolute; left: 0; top: 0; bottom: 0; width: 38px;
    background: var(--rose);
  }
  .front-band-edge {
    position: absolute; left: 38px; top: 0; bottom: 0; width: 7px;
    background: var(--rose-light);
  }
  .front-mark {
    position: absolute; left: 6px; top: 31px; width: 66px; height: 66px;
    border-radius: 50%; background: var(--paper);
  }
  .brand-name {
    position: absolute;
    font-family: "Advent Pro", sans-serif;
    font-weight: 300;
    color: var(--rose);
    letter-spacing: 6px;
    line-height: 1;
  }
  .card-front .brand-name { left: 112px; top: 38px; font-size: 56px; }
  .holder-name {
    position: absolute; left: 113px; top: 110px;
    font-weight: 700; font-size: 20px; letter-spacing: 1px;
    color: var(--rose);
  }
  .holder-role {
    position: absolute; left: 113px; top: 136px;
    font-weight: 500; font-size: 15px; letter-spacing: 1px;
    color: var(--ink);
  }
  .address {
    position: absolute; right: 31px; top: 176px;
    text-align: right; font-size: 14px; line-height: 19px; color: var(--ink);
  }
  .contact-list {
    position: absolute; right: 32px; top: 222px;
    list-style: none; text-align: right;
    font-size: 14px; line-height: 19.2px; color: var(--ink);
  }
  .contact-list li { display: flex; justify-content: flex-end; align-items: center; gap: 8px; }
  .contact-list svg { width: 12px; height: 12px; fill: var(--rose); }
  .card-back {
    left: 311px; top: 472px; width: 600px; height: 341px;
    background: var(--night);
  }
  .back-mark {
    position: absolute; left: 249px; top: 78px; width: 100px; height: 100px;
    border-radius: 50%; border: 3px solid var(--rose);
  }
  .card-back .brand-name {
    left: 0; right: 0; top: 212px; text-align: center; font-size: 50px;
  }
  .back-url {
    position: absolute; left: 0; right: 0; top: 296px; text-align: center;
    font-size: 13px; letter-spacing: 5px; color: var(--white);
  }
</style>
</head>
<body>
  <section class="card card-front">
    <div class="front-band"></div>
    <div class="front-band-edge"></div>
    <div class="front-mark"></div>
    <div class="brand-name">GLIMORA</div>
    <div class="holder-name">CLARA BENSON</div>
    <div class="holder-role">CEO/FOUNDER</div>
    <div class="address">214 Willowbrook Court<br>Juneau, Alaska 99801</div>
    <ul class="contact-list">
      <li>555 214 0187
        <svg viewBox="0 0 12 12"><path d="M2.5 1l2 2.2-1 1.3c.8 1.6 2 2.8 3.5 3.5l1.3-1 2.2 2-1 1.8C5 10.5 1.5 7 .8 2z"/></svg></li>
      <li>555 362 7740
        <svg viewBox="0 0 12 12"><path d="M3 0h6v12H3zM4 1.5v8h4v-8z"/></svg></li>
      <li>555 908 3316
        <svg viewBox="0 0 12 12"><path d="M3 1h6v3H3zM1 4.5h10v5H9v1.5H3V9.5H1zM4 8v2h4V8z"/></svg></li>
      <li>info@glimora-example.com
        <svg viewBox="0 0 12 12"><path d="M0 2.5h12v7H0zM1 3.3l5 3.4 5-3.4z" fill-rule="evenodd"/></svg></li>
      <li>www.glimora-example.com
        <svg viewBox="0 0 12 12"><circle cx="6" cy="6" r="6"/><path d="M1 6h10M6 1c2 2 2 8 0 10M6 1c-2 2-2 8 0 10" stroke="#f4f4f4" stroke-width=".8" fill="none"/></svg></li>
    </ul>
  </section>

  <section class="card card-back">
    <div class="back-mark"></div>
    <div class="brand-name">GLIMORA</div>
    <div class="back-url">www.glimora-example.com</div>
  </section>
</body>
</html>
```